BRISKEL Need a luxury modern business card designed.

Need a luxury modern business card designed. refer to the uploaded files for the company name and logo in the zip file under source files. i will making my descion on monday. so please send in before then so if we need to edit we will have the time. we have a trade show coming up and im on a deadline for printer.

Target Market(s)

high end clients

Contact Information for Business Card

Company nAme and logo. Tobias Fennick Co-Founder / Project Manager Office # 555-318-7094 Cell # 555-642-1586 BRISKEL.CA Tobias@briskel-example.ca

Font styles to use
Other font styles liked:
• Modern

Requirements
Must have
• Company name and logo, contact info, using the black, gold and white color scheme.

```html
<!DOCTYPE html>
<html lang="en">
<head>
<meta charset="utf-8">
<title>BRISKEL Business Card</title>
<link href="https://fonts.googleapis.com/css2?family=Josefin+Sans:wght@300;400&family=Poppins:wght@300;400;500&display=swap" rel="stylesheet">
<style>
  :root {
    --stage: #2a2a2c;
    --card: #1f1f21;
    --card-deep: #19191b;
    --pattern: #262628;
    --gold: #b39b66;
    --white: #f2f2f0;
    --soft: #c9c9c6;
    --rule: #8d8d8a;
  }
  * { margin: 0; padding: 0; box-sizing: border-box; }
  html, body { width: 1200px; height: 800px; overflow: hidden; background: var(--stage); }
  .stage {
    width: 1200px; height: 800px;
    display: flex; align-items: center; justify-content: center; gap: 40px;
  }
  .card {
    position: relative; width: 540px; height: 309px;
    border-radius: 22px; background: var(--card); overflow: hidden;
    box-shadow: 0 18px 40px rgba(0,0,0,.45);
    color: var(--white);
  }
  /* front */
  .card-pattern {
    position: absolute; inset: 0;
    background: linear-gradient(135deg, var(--pattern) 0%, var(--card-deep) 55%, var(--pattern) 100%);
  }
  .front-lockup {
    position: absolute; left: 0; right: 0; top: 92px;
    text-align: center; font-family: "Josefin Sans", sans-serif;
  }
  .wordmark {
    font-weight: 300; font-size: 60px; letter-spacing: 10px;
    color: var(--white); line-height: 1;
  }
  .tagline-row {
    display: flex; align-items: center; justify-content: center; gap: 10px;
    margin-top: 10px;
  }
  .tagline-row .rule { height: 1px; width: 70px; background: var(--rule); }
  .tagline {
    font-family: "Poppins", sans-serif; font-weight: 500;
    font-size: 11px; letter-spacing: 5px; color: var(--soft);
  }
  .front-url {
    margin-top: 12px; font-family: "Poppins", sans-serif; font-weight: 400;
    font-size: 11px; letter-spacing: 9px; color: var(--gold);
  }
  /* back */
  .back-brand {
    position: absolute; right: 34px; top: 36px; text-align: right;
    font-family: "Josefin Sans", sans-serif;
  }
  .brand-mark {
    display: inline-block; width: 26px; height: 26px;
    border: 2px solid var(--gold); margin-bottom: 12px;
  }
  .back-brand .wordmark { font-size: 40px; letter-spacing: 6px; }
  .back-brand .tagline-row { justify-content: flex-end; margin-top: 6px; }
  .back-brand .tagline { font-size: 8px; letter-spacing: 3.5px; }
  .back-brand .tagline-row .rule { width: 40px; }
  .address {
    position: absolute; right: 34px; top: 172px; text-align: right;
    font-family: "Poppins", sans-serif; font-size: 11px; line-height: 1.6; color: var(--soft);
  }
  .person { position: absolute; left: 34px; top: 150px; font-family: "Poppins", sans-serif; }
  .person-name { font-size: 20px; font-weight: 400; letter-spacing: .5px; line-height: 1.1; }
  .person-name .surname { color: var(--gold); }
  .person-role { font-size: 11.5px; font-weight: 300; color: var(--soft); margin-top: 4px; }
  .person-rule { width: 90px; height: 2px; background: var(--white); margin-top: 8px; }
  .contacts {
    position: absolute; left: 34px; bottom: 24px; list-style: none;
    font-family: "Poppins", sans-serif; font-size: 11.5px; color: var(--white);
  }
  .contacts li { display: flex; align-items: center; gap: 9px; line-height: 1.75; }
  .contacts svg { width: 12px; height: 12px; fill: var(--gold); flex: none; }
</style>
</head>
<body>
<main class="stage">
  <section class="card card-front" aria-label="Card front">
    <div class="card-pattern" role="img" aria-label="Faint tonal geometric square pattern across the card"></div>
    <div class="front-lockup">
      <div class="wordmark">BRISKEL</div>
      <div class="tagline-row"><span class="rule"></span><span class="tagline">LUXURY LANDSCAPES</span><span class="rule"></span></div>
      <div class="front-url">BRISKEL.CA</div>
    </div>
  </section>

  <section class="card card-back" aria-label="Card back">
    <div class="back-brand">
      <span class="brand-mark"></span>
      <div class="wordmark">BRISKEL</div>
      <div class="tagline-row"><span class="rule"></span><span class="tagline">LUXURY LANDSCAPES</span></div>
    </div>
    <p class="address">48 Harlow Crescent, Unit 7<br>Ridgeview, ON. K9R 2T5</p>

    <div class="person">
      <div class="person-name">TOBIAS <span class="surname">FENNICK</span></div>
      <div class="person-role">Co-Founder / Project Manager</div>
      <div class="person-rule"></div>
    </div>

    <ul class="contacts">
      <li><svg viewBox="0 0 12 12" aria-hidden="true"><path d="M1 4c0-2 2-3 5-3s5 1 5 3l-2 1-1-1.5H4L3 5zM3 6h6l1 5H2z"/></svg>555-318-7094</li>
      <li><svg viewBox="0 0 12 12" aria-hidden="true"><path d="M3 0h6v12H3zM4 1.5v8h4v-8z"/></svg>555-642-1586</li>
      <li><svg viewBox="0 0 12 12" aria-hidden="true"><circle cx="6" cy="6" r="5.5"/></svg>BRISKEL.CA</li>
      <li><svg viewBox="0 0 12 12" aria-hidden="true"><path d="M0 2h12v8H0zM1 3l5 4 5-4z"/></svg>Tobias@briskel-example.ca</li>
    </ul>
  </section>
</main>
</body>
</html>
```